Sunset Harbor Living Web Page

We need a web page design that has two intro pages - first being a 'home page', then a link to the second page that has the 'content tabs' and a 'call to action' (see below).

The business helps people that wish to retire to S.E.Asia (Thailand, Malaysia, Indonesia,The Philippines etc) - to enjoy the lifestyle and the remaining years of their lives. What attracts S.E.Asia to many people is the lower cost, the atmoshpere and beauty of the tropics and the vibrancy of the various countries.

People that are wishing to make the most of their retirement and are adventurous at a great bargain compared to the cost of their own countries will be interested.

We help them achieve this - visa, financials (tax, gov't payments etc), introduce them to the right people for property, clubs, retirement facilities, insurance and so forth.

Therefore we are providing an extremely wide ranging service and this site will provide broad but general information only - with a call to action to come and see us for more specific information and how we can help them specifically.

This site will be predominantly for travel and lifestyle, it will be linked with another financial services (financial planning) site later down the track.

The colour scheme is dark green and blue - as per the attached logo design. Photos and background just think lifestyle and S.E.Asia - beaches/mountains/water/recreational activities for retirees.

Target market is mostly those coming up to retirement to those that are already retired. But we also expect to have some interest with younger people that would like to find out more and plan for the future. So a broad age group but I would say mostly 40-70 yrs old.

On the first (Home) page we would like our company name 'Sunset Harbor Living', our logo (which will be on all pages) and a statement such as: “Imagine a retirement where your dreams are brought to life, and you have never felt more alive. Let us show you how”. Then a link to the second page.

We would like an uncluttered site. On the second (contents) page the tabs would be:

- Visa
- Property
- Financials
- Travel
- Insurance & Healthcare
- Medical Tourism
- Cost of living
- Weekly Blogs and articles
- Sunset Harbor Living story

We would also like a call to action on the second page - asking them to leave their contact details if they wish to learn more or sign up to our weekly newsletter/blog.

We are open to suggestions and your imaginations.

Thank you
Malcolm

Font styles to use
Serif
Script

Colors
0255a3
3377b5
00a990
9bcb3c
abd036
33b8a4
85abd2
cadf82
86cfc6

Requirements
Must have
• I have been asked by the web designer to receive a 'Web Font' so that we can 'get off of Zentrofy'. Hope that makes sense.

```html
<!DOCTYPE html>
<html lang="en">
<head>
<meta charset="utf-8">
<title>Sunset Harbor Living</title>
<link rel="stylesheet" href="https://fonts.googleapis.com/css2?family=Cinzel:wght@700&family=Mulish:wght@700;800&display=swap">
<style>
  :root {
    --sky-top: #4f8fbf;
    --sky-mid: #b9c9cf;
    --glow: #f6dfae;
    --sea: #3a5f78;
    --sand: #b3744a;
    --sand-dark: #5a3420;
    --brand-green: #12a54a;
    --headline-green: #0e8a33;
    --headline-edge: #022b10;
    --button-blue: #0a93d8;
    --white: #ffffff;
  }
  * { margin: 0; padding: 0; box-sizing: border-box; }
  html, body { width: 1200px; height: 683px; overflow: hidden; }
  body { font-family: "Mulish", sans-serif; background: var(--sky-top); }

  .hero {
    position: relative;
    width: 1200px;
    height: 683px;
    overflow: hidden;
  }
  .hero-photo {
    position: absolute;
    inset: 0;
    background:
      radial-gradient(ellipse 380px 220px at 560px 400px, rgba(255,236,190,0.95), rgba(255,220,160,0) 70%),
      linear-gradient(180deg,
        var(--sky-top) 0%,
        #8fb0c6 22%,
        var(--sky-mid) 40%,
        var(--glow) 55%,
        var(--sea) 58%,
        #6f8696 68%,
        #d6a373 74%,
        var(--sand) 86%,
        var(--sand-dark) 100%);
  }

  .brand {
    position: absolute;
    top: 155px;
    left: 0;
    width: 100%;
    text-align: center;
  }
  .brand-name {
    font-family: "Mulish", sans-serif;
    font-weight: 800;
    font-size: 34px;
    line-height: 1;
    letter-spacing: -0.3px;
    color: var(--white);
  }

  .headline {
    position: absolute;
    top: 330px;
    left: 0;
    width: 100%;
    text-align: center;
    font-family: "Cinzel", serif;
    font-weight: 700;
    font-size: 31px;
    line-height: 38px;
    color: var(--headline-green);
    text-shadow:
      1px 1px 0 var(--headline-edge),
      -1px -1px 0 var(--headline-edge),
      1px -1px 0 var(--headline-edge),
      -1px 1px 0 var(--headline-edge),
      0 0 6px rgba(0,0,0,0.45);
  }

  .cta-button {
    position: absolute;
    top: 476px;
    left: 441px;
    width: 333px;
    height: 55px;
    display: flex;
    align-items: center;
    border: 2px solid var(--white);
    border-radius: 6px;
    background: var(--button-blue);
    color: var(--white);
    text-decoration: none;
    overflow: hidden;
  }
  .cta-label {
    flex: 1;
    padding-left: 14px;
    font-weight: 700;
    font-size: 24px;
    letter-spacing: 0.2px;
    white-space: nowrap;
  }
  .cta-arrow {
    width: 54px;
    height: 55px;
    margin-right: -2px;
    display: flex;
    align-items: center;
    justify-content: center;
    background: var(--brand-green);
    border-left: 2px solid var(--white);
    border-radius: 28px 0 0 28px;
  }
</style>
</head>
<body>
  <main class="hero">
    <div class="hero-photo" role="img" aria-label="Retired couple seated in striped beach chairs on the sand, facing the sea at sunset"></div>

    <header class="brand">
      <div class="brand-name">Sunset Harbor Living</div>
    </header>

    <h1 class="headline">
      Imagine A Retirement Where Your Dreams Are<br>
      Brought To Life,<br>
      &amp; You Have Never Felt More Alive
    </h1>

    <a class="cta-button" href="#contents">
      <span class="cta-label">Let Us Show You How</span>
      <span class="cta-arrow">
        <svg width="26" height="22" viewBox="0 0 26 22" aria-hidden="true">
          <polyline points="4,3 12,11 4,19" fill="none" stroke="#ffffff" stroke-width="2"/>
          <polyline points="13,3 21,11 13,19" fill="none" stroke="#ffffff" stroke-width="2"/>
        </svg>
      </span>
    </a>
  </main>
</body>
</html>
```